Business card design

I am open to ideas. I was thinking of a vertical design, turning the name 90 degrees and placing it on the left edge, then some clipped portion of the fabulous tree with contact info on the bottom -- special emphasis on Web address:WhimBeads.comFor All Your Beading Needs121 E. Cotati AveCotati, CA 94931(707) 664-8343

```html
<!DOCTYPE html>
<html lang="en">
<head>
<meta charset="utf-8">
<title>Fern Glass Co — Business Card</title>
<link rel="stylesheet" href="https://fonts.googleapis.com/css2?family=Libre+Baskerville:wght@400;700&display=swap">
<style>
  :root {
    --page-bg: #d8d3cc;
    --frost-top: #ecebe9;
    --frost-bottom: #d6d1cb;
    --ink: #1b1b1b;
    --panel: #141414;
    --panel-soft: #2a2a2a;
    --text-light: #f1efea;
    --text-muted: #d9d6d0;
    --violet: #5b4486;
    --blue: #3a4fa0;
    --green: #3f8a2c;
    --yellow: #d9a21a;
    --orange: #e0761c;
    --red: #c8261e;
    --silver: #efece6;
  }
  * { box-sizing: border-box; margin: 0; padding: 0; }
  html, body {
    width: 970px; height: 1200px; overflow: hidden;
    background: var(--page-bg);
    font-family: "Libre Baskerville", Georgia, serif;
  }
  .card {
    position: absolute; left: 195px; top: 80px;
    width: 580px; height: 1040px;
    border-radius: 28px; overflow: hidden;
    background: linear-gradient(180deg, var(--frost-top), var(--frost-bottom));
    box-shadow: 0 14px 40px rgba(0,0,0,.22);
  }
  .card-shape { position: absolute; inset: 0; }
  .brand {
    position: absolute; top: 330px; left: 0; width: 100%;
    display: flex; align-items: center; justify-content: center; gap: 18px;
  }
  .brand-dot { width: 26px; height: 26px; border-radius: 50%; background: var(--ink); }
  .brand-name { font-size: 44px; font-weight: 400; color: var(--ink); letter-spacing: .5px; }
  .person { position: absolute; top: 590px; width: 100%; text-align: center; color: var(--text-light); }
  .person-name { font-size: 31px; font-weight: 700; }
  .person-role { font-size: 19px; margin-top: 10px; color: var(--text-muted); }
  .contact-row {
    position: absolute; width: 100%; text-align: center;
    color: var(--text-light); font-size: 25px; line-height: 1.32;
  }
  .contact-row.phone { top: 754px; }
  .contact-row.address { top: 868px; }
  .divider { position: absolute; left: 120px; width: 340px; height: 52px; }
  .divider.phone { top: 696px; }
  .divider.address { top: 810px; }
  .web-strip {
    position: absolute; left: 0; bottom: 0; width: 100%; height: 66px;
    background: linear-gradient(90deg, var(--violet), var(--green) 35%, var(--yellow) 65%, var(--orange) 80%, var(--red));
    border-top: 6px solid var(--silver);
    display: flex; align-items: center; justify-content: center;
  }
  .web-address { font-size: 25px; font-weight: 700; letter-spacing: 6px; color: var(--ink); }
</style>
</head>
<body>
  <div class="card">
    <svg class="card-shape" width="580" height="1040" viewBox="0 0 580 1040" aria-hidden="true">
      <defs>
        <linearGradient id="swoosh" x1="0" x2="1">
          <stop offset="0" stop-color="#2f6e1e"/>
          <stop offset=".45" stop-color="#8a8a1c"/>
          <stop offset=".75" stop-color="#d0781a"/>
          <stop offset="1" stop-color="#b8431a"/>
        </linearGradient>
        <linearGradient id="panelFill" x1="0" y1="0" x2="0" y2="1">
          <stop offset="0" stop-color="#0d0d0d"/>
          <stop offset=".6" stop-color="#1e1e1e"/>
          <stop offset="1" stop-color="#2c2c2c"/>
        </linearGradient>
      </defs>
      <path d="M0 575 C 120 500, 300 470, 580 535 L 580 555 C 330 500, 150 520, 0 600 Z" fill="url(#swoosh)"/>
      <path d="M0 600 C 150 520, 330 500, 580 555 L 580 1040 L 0 1040 Z" fill="url(#panelFill)"/>
      <path d="M115 567 C 260 515, 420 510, 580 548" fill="none" stroke="#e8e2da" stroke-width="3" opacity=".75"/>
    </svg>

    <div class="brand">
      <span class="brand-dot"></span>
      <span class="brand-name">Fern Glass Co</span>
    </div>

    <div class="person">
      <p class="person-name">Jordan Hale</p>
      <p class="person-role">Manager</p>
    </div>

    <svg class="divider phone" viewBox="0 0 340 52" aria-hidden="true">
      <defs>
        <linearGradient id="lineL" x1="0" x2="1"><stop offset="0" stop-color="#5b4486" stop-opacity="0"/><stop offset=".4" stop-color="#3a4fa0"/><stop offset="1" stop-color="#3f8a2c"/></linearGradient>
        <linearGradient id="lineR" x1="0" x2="1"><stop offset="0" stop-color="#d9a21a"/><stop offset=".6" stop-color="#e0761c"/><stop offset="1" stop-color="#c8261e" stop-opacity="0"/></linearGradient>
      </defs>
      <line x1="0" y1="26" x2="140" y2="26" stroke="url(#lineL)" stroke-width="2"/>
      <line x1="200" y1="26" x2="340" y2="26" stroke="url(#lineR)" stroke-width="2"/>
      <circle cx="170" cy="26" r="24" fill="#f4f2ee"/>
      <circle cx="170" cy="26" r="19" fill="none" stroke="#444" stroke-width="2"/>
      <path d="M162 16 l5 -2 l3 7 l-3 3 q2 5 6 8 l3 -3 l7 3 l-2 5 q-10 2 -17 -9 q-5 -7 -2 -12 z" fill="#333"/>
    </svg>
    <p class="contact-row phone">(707) 555-0192</p>

    <svg class="divider address" viewBox="0 0 340 52" aria-hidden="true">
      <line x1="0" y1="26" x2="140" y2="26" stroke="url(#lineL)" stroke-width="2"/>
      <line x1="200" y1="26" x2="340" y2="26" stroke="url(#lineR)" stroke-width="2"/>
      <circle cx="170" cy="26" r="24" fill="#f4f2ee"/>
      <circle cx="170" cy="26" r="19" fill="none" stroke="#444" stroke-width="2"/>
      <path d="M170 38 C 163 29, 161 25, 161 21 a9 9 0 0 1 18 0 c0 4 -2 8 -9 17 z" fill="#333"/>
      <circle cx="170" cy="21" r="3.5" fill="#f4f2ee"/>
    </svg>
    <p class="contact-row address">348 W. Brindle Ave, Larkview<br>CA 94952</p>

    <div class="web-strip">
      <span class="web-address">FernGlassco.com</span>
    </div>
  </div>
</body>
</html>
```